Specialised investor in e-mobility and energy wants business card design

We need a business card design that fits our existing corporate design. <The look and feel must be 'sharp'/'clean', dynamic, communicate momentum, professionalism etc (as one would imagine from a firm in the financial sector). We like the idea of a reverse-side of the card that includes the logo, and the name and contact details on the other. We expect the deliverable to be whatever format might be required to be able to get cards printed directly by a service such as kelmo press. Our website is www.zub.capital

```html
<!DOCTYPE html>
<html lang="en">
<head>
<meta charset="utf-8">
<title>Zub Capital – Business Card</title>
<link rel="stylesheet" href="https://fonts.googleapis.com/css2?family=Montserrat:wght@400;500;800&display=swap">
<style>
  :root {
    --bg: #1e1e1e;
    --forest: #344f25;
    --leaf: #7ab648;
    --ink: #3a3a3a;
    --paper: #ffffff;
  }
  * { margin: 0; padding: 0; box-sizing: border-box; }
  html, body { width: 1200px; height: 988px; overflow: hidden; background: var(--bg); }
  body { position: relative; font-family: "Montserrat", sans-serif; }

  .card {
    position: absolute;
    left: 250px;
    width: 700px;
    height: 400px;
    border-radius: 26px;
    overflow: hidden;
    box-shadow: 0 14px 30px rgba(0,0,0,.45);
  }
  .card--front { top: 70px; background: var(--forest); }
  .card--back { top: 518px; background: var(--paper); }

  .wordmark {
    position: absolute;
    left: 50%; top: 50%;
    transform: translate(-50%, -50%);
    display: flex;
    align-items: center;
    gap: 26px;
    white-space: nowrap;
  }
  .wordmark-dot {
    width: 34px; height: 34px;
    background: var(--leaf);
    flex: none;
  }
  .brand-name {
    color: var(--paper);
    font-weight: 400;
    font-size: 84px;
    letter-spacing: 1px;
    line-height: 1;
  }

  .back-band {
    position: absolute; left: 0; top: 0; bottom: 0; width: 205px;
    background: var(--forest);
  }
  .band-mark {
    position: absolute; left: 50%; top: 50%;
    transform: translate(-50%, -50%) rotate(90deg);
    display: flex; align-items: center; gap: 16px;
    white-space: nowrap;
  }
  .band-mark .wordmark-dot { width: 20px; height: 20px; }
  .band-name {
    color: var(--paper);
    font-weight: 400;
    font-size: 46px;
    line-height: 1;
  }

  .details { position: absolute; left: 250px; top: 58px; color: var(--ink); }
  .person { font-weight: 800; font-size: 34px; letter-spacing: 1px; color: var(--forest); line-height: 1; }
  .person .surname { color: var(--leaf); }
  .role { font-size: 19px; margin-top: 6px; }

  .contact-list { list-style: none; margin-top: 24px; }
  .contact-list li { display: flex; align-items: center; gap: 12px; font-size: 19px; height: 32px; }
  .contact-list svg { width: 16px; height: 16px; fill: var(--leaf); flex: none; }

  .address { margin-top: 20px; font-size: 19px; line-height: 1.4; }
</style>
</head>
<body>

<section class="card card--front" aria-label="Card front">
  <div class="wordmark">
    <span class="wordmark-dot" aria-hidden="true"></span>
    <p class="brand-name">ZUB capital</p>
  </div>
</section>

<section class="card card--back" aria-label="Card back">
  <div class="back-band">
    <div class="band-mark">
      <span class="wordmark-dot" aria-hidden="true"></span>
      <p class="band-name">ZUB capital</p>
    </div>
  </div>

  <div class="details">
    <h1 class="person">MARTIN <span class="surname">KERROW</span></h1>
    <p class="role">Director/Founder</p>

    <ul class="contact-list">
      <li>
        <svg viewBox="0 0 16 16" aria-hidden="true"><path d="M3.5 1l2.5 3-1.5 1.5c.8 2 2.6 3.8 4.5 4.5L10.5 8.5l3 2.5-1.5 3C7 14 2 9 2 3z"/></svg>
        123-480-2291
      </li>
      <li>
        <svg viewBox="0 0 16 16" aria-hidden="true"><path d="M1 3h14v10H1z M1 3l7 6 7-6" stroke="#fff" stroke-width="1"/></svg>
        info@zub.capital
      </li>
      <li>
        <svg viewBox="0 0 16 16" aria-hidden="true"><circle cx="8" cy="8" r="7"/><path d="M1 8h14M8 1c3 3 3 11 0 14M8 1c-3 3-3 11 0 14" stroke="#fff" stroke-width="1" fill="none"/></svg>
        www.zub.capital
      </li>
    </ul>

    <p class="address">1234 Street Name<br>Country Name AB 5748</p>
  </div>
</section>

</body>
</html>
```